A parent Company needs a website as a leading diversified business in industrial Conglomerates in Af

Velkor Group is a private (Holding) limited liability company incorporated under the Companies Code, 1963 (Act 179) in November, 2013 to following the speedy growth in numbers of its current subsidiaries which has been founded several years ago with an emerging force to become one of the largest and a leading diversified business in industrial Conglomerates in Africa.
The Group which is 100% wholly owned indigenous Ghanaian Company focuses on provision of local, value-added products and services that meet the needs of the African population. The Group is headquartered in Accra, Ghana with interests across a range of sectors in Africa.
We are currently into Food & Beverage, Real Estate Development, Transportation, Health Care, Consumer Products Distribution, Agro Processing, Manufacturing, ICT, Exports & Import, and still counting.
In the next 3 years, we shall announce our ambitions to enter Ghana's largest Oil and Gas industry, playing a strategic role in the petroleum sector with strategic alliances, and help build Ghana's biggest and most important Energy sector in the country.
Inspired by billionaires Tom Prewitt, Harlan Voskel, and Emeka Ofodile, Velkor Group (Velkor Foundation) is committed to making a name for itself on the philanthropic circuit and has given away privately and still given to the cause to the needy in the society and some specific social causes in Ghana.
The company is managed by a 5 member board and a 2 member advisory experts who are non-board members.
The company has a vision, mission and it is guided by its core values.
We would like to see a designs that is very professional and looks corporate and can attract investors and partners. It must communicate financial safety and growth and must reflect our logo colors.

```html
<!DOCTYPE html>
<html lang="en">
<head>
<meta charset="utf-8">
<title>Velkor Group</title>
<link href="https://fonts.googleapis.com/css2?family=Open+Sans:wght@400;600&family=Noto+Serif:ital@1&display=swap" rel="stylesheet">
<style>
:root{
  --bg:#efefef;
  --page:#ffffff;
  --header:#f2f2f2;
  --dark:#3b3b3b;
  --darker:#2e2e2e;
  --blue:#1f8fd8;
  --red:#d6304a;
  --text:#444;
  --muted:#9a9a9a;
  --line:#e2e2e2;
  --card:#ececec;
}
*{box-sizing:border-box;margin:0;padding:0}
html,body{width:738px;height:1200px;overflow:hidden}
body{background:var(--bg);font-family:"Open Sans",Arial,sans-serif;color:var(--text)}
.page{position:absolute;left:68px;top:0;width:602px;height:1200px;background:var(--page)}
.abs{position:absolute}

/* top bar */
.topbar{left:0;top:0;width:602px;height:29px;background:var(--dark);border-top:2px solid var(--blue);display:flex;align-items:center;justify-content:space-between;padding:0 10px;font-size:7px;color:#fff;white-space:nowrap}
.topbar ul{list-style:none;display:flex}
.topbar li{padding:0 8px;border-right:1px solid #777}
.topbar li:first-child{padding-left:0}

/* header */
.header{left:0;top:29px;width:602px;height:109px;background:var(--header)}
.brand{left:10px;top:62px;display:flex;flex-direction:column}
.brand-row{display:flex;align-items:center;gap:6px}
.brand-mark{width:14px;height:14px;border-radius:50%;background:var(--blue)}
.brand-name{font-size:14px;font-weight:400;color:var(--darker);letter-spacing:.3px;white-space:nowrap}
.brand-tag{font-size:7.5px;color:var(--red);margin-top:1px;white-space:nowrap}
.contacts{right:24px;top:38px;display:flex;gap:6px;white-space:nowrap}
.pill{background:#e0e0e0;border-radius:8px;font-size:7px;color:#666;padding:3px 6px}
.social{right:26px;top:59px;display:flex;gap:7px}
.social span{width:13px;height:13px;border-radius:50%;background:#8a8a8a}

/* nav */
.nav{left:0;top:138px;width:602px;height:33px;background:var(--dark);display:flex;align-items:center}
.nav .home{flex:0 0 40px;height:33px;background:var(--darker);border-top:2px solid var(--blue);display:flex;align-items:center;justify-content:center}
.nav a{color:#fff;text-decoration:none;font-size:9.6px;height:33px;line-height:33px;border-right:1px solid #4d4d4d;white-space:nowrap;text-align:center;flex:0 0 auto}
.search{margin-left:9px;width:152px;height:21px;background:#4a4a4a;display:flex;align-items:center;justify-content:space-between;padding:0 7px;font-size:7px;color:#aaa;white-space:nowrap}

/* hero */
.hero{left:0;top:171px;width:602px;height:295px;background:linear-gradient(135deg,#c9c3b8,#8c8479 45%,#4a4440 75%,#2f2b29)}
.caption{left:18px;top:180px;width:214px;background:rgba(30,30,30,.85);border-top:2px solid var(--blue);padding:8px 8px 6px;font-family:"Noto Serif",Georgia,serif;font-style:italic;font-size:7.6px;line-height:1.6;color:#fff}
.arrows{left:18px;top:232px;width:36px;height:20px;background:rgba(30,30,30,.85);display:flex;align-items:center;justify-content:center;gap:8px}

/* tagline */
.tagline{left:0;top:466px;width:602px;height:38px;background:#f4f4f4;display:flex;align-items:center;justify-content:space-between;padding:0 14px 0 8px;white-space:nowrap}
.tagline h1{font-size:17px;font-weight:400;color:var(--darker)}
.tagline h1 em{font-style:normal;color:var(--red)}
.btn{background:var(--dark);color:#fff;font-size:10.5px;padding:5px 12px;border-radius:2px}

.section-title{font-size:12px;color:var(--darker);font-weight:400;white-space:nowrap}

/* services */
.service{width:190px;display:flex;gap:10px}
.service .icon{flex:0 0 32px;height:32px;background:var(--dark);border-radius:3px;display:flex;align-items:center;justify-content:center}
.service h3{font-size:9px;font-weight:600;color:var(--darker);margin-top:-2px;white-space:nowrap}
.service p{font-size:7px;line-height:1.4;color:var(--muted);margin-top:3px}

.rule{height:1px;background:var(--line)}

/* portfolio */
.dots{right:48px;top:702px;display:flex;gap:2px}
.dots i{width:6px;height:6px;border-radius:50%;background:var(--dark)}
.dots i:first-child{background:var(--blue)}
.pager{right:12px;top:695px;display:flex;gap:2px}
.pager span{width:16px;height:16px;background:var(--dark);display:flex;align-items:center;justify-content:center}
.work{width:138px;top:720px}
.work .shot{height:114px}
.work .label{height:37px;background:var(--card);display:flex;align-items:center;justify-content:center;font-size:10px;color:#555;white-space:nowrap}
.work.active .shot{border-top:2px solid var(--blue)}
.work.active .label{color:var(--blue)}

/* quote */
.quote{left:16px;top:908px;width:560px;display:flex;gap:6px;font-family:"Noto Serif",Georgia,serif;font-style:italic;font-size:9.6px;line-height:1.45;color:#555}
.quote b{font-size:22px;line-height:.9;color:#bbb;font-weight:400}

/* accordion */
.acc{left:12px;top:976px;width:220px}
.acc-item{display:flex;align-items:center;gap:6px;font-size:9.6px;color:var(--darker);height:27.5px;border-bottom:1px solid var(--line);white-space:nowrap}
.acc-item:first-child{border:none;height:auto}
.acc-toggle{width:14px;height:14px;border:1px solid #555;border-radius:50%;font-size:11px;line-height:11px;text-align:center;color:#555}
.acc p{font-size:7px;line-height:1.75;color:#777;padding:9px 0 12px 20px;border-bottom:1px solid var(--line)}

/* blog */
.blog{left:253px;top:976px;width:223px}
.post{display:flex;gap:10px;padding:8px 0;border-bottom:1px solid var(--line)}
.post:last-child{border:none}
.post .thumb{flex:0 0 48px;height:38px;border:2px solid #eee}
.post h4{font-size:8.2px;font-weight:400;line-height:1.5;color:var(--darker)}
.post small{font-family:"Noto Serif",Georgia,serif;font-size:6.4px;color:#777;white-space:nowrap}
.post small em{font-style:normal;color:var(--red)}

/* partners */
.partners{left:490px;top:976px;width:100px}
.slider{margin-top:10px;background:#e6e6e6;height:158px;padding:10px 0;position:relative}
.badge{height:68px;background:#2d1a2e;display:flex;align-items:center;justify-content:center}
.badge+.badge{background:#0b0b0b}
.badge span{width:22px;height:22px;border-radius:50%;background:#7c3f7a}
.badge+.badge span{background:#555;border-radius:3px}

/* footer */
.footer{left:0;top:1173px;width:602px;height:27px;background:var(--dark);display:flex;align-items:center;justify-content:space-between;padding:0 16px 0 18px;font-size:6.8px;color:#ddd;white-space:nowrap}
</style>
</head>
<body>
<div class="page">

  <div class="abs topbar">
    <ul><li>Home</li><li>About Us</li><li>Services</li><li>Contact Us</li></ul>
    <span>Lorem ipsum dolor sit amet consectetur adipsicing elit.</span>
  </div>

  <header class="abs header">
    <div class="abs brand">
      <div class="brand-row"><span class="brand-mark"></span><span class="brand-name">VELKOR GROUP</span></div>
      <div class="brand-tag">Tenacity, Integrity &amp; Passion</div>
    </div>
    <div class="abs contacts"><span class="pill">Call | 0800-555-0142</span><span class="pill">Email | info@velkorgroup.com</span></div>
    <div class="abs social"><span></span><span></span><span></span><span></span><span></span><span></span></div>
  </header>

  <nav class="abs nav">
    <div class="home"><svg width="16" height="14" viewBox="0 0 16 14"><path d="M8 1 1 7h2v6h4V9h2v4h4V7h2z" fill="#fff"/></svg></div>
    <a style="width:54px">Home</a><a style="width:65px">About Us</a><a style="width:79px">Our Services</a><a style="width:62px">Portfolio</a><a style="width:65px">Our Blog</a><a style="width:70px">Contact Us</a>
    <div class="search">Search here<svg width="10" height="10" viewBox="0 0 10 10"><circle cx="4" cy="4" r="3" stroke="#aaa" stroke-width="1.4" fill="none"/><path d="M6.3 6.3 9.3 9.3" stroke="#aaa" stroke-width="1.6"/></svg></div>
  </nav>

  <section class="abs hero" role="img" aria-label="Business team smiling around a meeting table">
    <div class="abs caption">Lorem ipsum dolor sit amet, consectetur adipisicing elit, sed do eiusmod tempor incididunt ut labore et dolore magna aliqua.</div>
    <div class="abs arrows"><svg width="5" height="8"><path d="M4 1 1 4l3 3" stroke="#fff" fill="none"/></svg><svg width="5" height="8"><path d="M1 1l3 3-3 3" stroke="#fff" fill="none"/></svg></div>
  </section>

  <div class="abs tagline">
    <h1>Velkor Group <em>Tenacity, Integrity &amp; Passion</em></h1>
    <span class="btn">Learn More</span>
  </div>

  <h2 class="abs section-title" style="left:12px;top:514px">Our Services</h2>

  <div class="abs service" style="left:12px;top:544px"><div class="icon"><svg width="18" height="16"><rect x="2" y="8" width="10" height="6" fill="#fff"/><path d="M6 2h10l-3 12H9z" fill="#fff"/></svg></div><div><h3>Food &amp; Beverage</h3><p>Lorem ipsum dolor sit amet, consecte-tur adipiscing elit, sed do eiusmod tempor magna aliqua...</p></div></div>
  <div class="abs service" style="left:208px;top:544px"><div class="icon"><svg width="18" height="16"><path d="M9 1 1 8h2v7h5v-4h2v4h5V8h2z" fill="#fff"/></svg></div><div><h3>Real Estate Development</h3><p>Lorem ipsum dolor sit amet, consecte-tur adipiscing elit, sed do eiusmod tempor magna aliqua...</p></div></div>
  <div class="abs service" style="left:410px;top:544px"><div class="icon"><svg width="18" height="16"><rect x="3" y="2" width="12" height="11" rx="2" fill="#fff"/><rect x="5" y="4" width="8" height="4" fill="#3b3b3b"/><rect x="3" y="13" width="3" height="2" fill="#fff"/><rect x="12" y="13" width="3" height="2" fill="#fff"/></svg></div><div><h3>Transportation</h3><p>Lorem ipsum dolor sit amet, consecte-tur adipiscing elit, sed do eiusmod tempor magna aliqua...</p></div></div>

  <div class="abs service" style="left:12px;top:618px"><div class="icon"><svg width="18" height="18"><rect x="8" y="1" width="2" height="16" fill="#fff"/><path d="M2 5h14l-3 3H5z" fill="#fff"/></svg></div><div><h3>Health Care</h3><p>Lorem ipsum dolor sit amet, consecte-tur adipiscing elit, sed do eiusmod tempor magna aliqua...</p></div></div>
  <div class="abs service" style="left:208px;top:618px"><div class="icon"><svg width="18" height="16"><path d="M2 4l7-3 7 3v9l-7 3-7-3z" fill="#fff"/><path d="M2 4l7 3 7-3M9 7v9" stroke="#3b3b3b" fill="none"/></svg></div><div><h3>Consumer Products Distribution</h3><p>Lorem ipsum dolor sit amet, consecte-tur adipiscing elit, sed do eiusmod tempor magna aliqua...</p></div></div>
  <div class="abs service" style="left:410px;top:618px"><div class="icon"><svg width="20" height="20"><circle cx="10" cy="10" r="7" stroke="#fff" stroke-width="2.2" stroke-dasharray="2 2.4" fill="none"/></svg></div><div><h3>Agro Processing</h3><p>Lorem ipsum dolor sit amet, consecte-tur adipiscing elit, sed do eiusmod tempor magna aliqua...</p></div></div>

  <div class="abs rule" style="left:12px;top:686px;width:578px"></div>

  <h2 class="abs section-title" style="left:12px;top:694px">Our Portfolio</h2>
  <div class="abs dots"><i></i><i></i><i></i><i></i></div>
  <div class="abs pager"><span><svg width="5" height="8"><path d="M4 1 1 4l3 3" stroke="#fff" fill="none"/></svg></span><span><svg width="5" height="8"><path d="M1 1l3 3-3 3" stroke="#fff" fill="none"/></svg></span></div>

  <div class="abs work active" style="left:12px"><div class="shot" role="img" aria-label="Model house held in an open hand" style="background:linear-gradient(#9fb58a,#6f8f55)"></div><div class="label">Lorem ipsum dolor</div></div>
  <div class="abs work" style="left:158px"><div class="shot" role="img" aria-label="Nurse caring for an elderly patient" style="background:linear-gradient(135deg,#e8e4de,#b9c4cc)"></div><div class="label">Lorem ipsum dolor</div></div>
  <div class="abs work" style="left:305px"><div class="shot" role="img" aria-label="Busy highway traffic at dusk" style="background:linear-gradient(#c88a2c,#5a3a14)"></div><div class="label">Lorem ipsum dolor</div></div>
  <div class="abs work" style="left:452px"><div class="shot" role="img" aria-label="Fried chicken, fries and a glass of beer" style="background:linear-gradient(135deg,#a8784a,#e4b860)"></div><div class="label">Lorem ipsum dolor</div></div>

  <div class="abs rule" style="left:12px;top:890px;width:578px"></div>
  <blockquote class="abs quote"><b>&ldquo;</b><span>Donec sed odio dui. Nulla vitae elit libero, a pharetra augue. Nullam id dolor id nibh ultricies vehicula ut id elit. posuere erat a ante venenatis dapibus posuere velit aliquet. Duis mollis, est non commodo luctus.</span></blockquote>
  <div class="abs rule" style="left:12px;top:956px;width:578px"></div>

  <div class="abs acc">
    <div class="acc-item"><span class="acc-toggle">&minus;</span>Lorem Ipsum Dolor Sit Amet?</div>
    <p>Donec sed odio dui. Nulla vitae elit libero, a pharetra augue. Nullam id dolor id nibh ultricies vehicula ut id elit. Integer posuere erat a ante venenatis dapibus posuere velit aliquet.</p>
    <div class="acc-item"><span class="acc-toggle">+</span>Consectetur Adipiscing</div>
    <div class="acc-item"><span class="acc-toggle">+</span>Elit Sed Do</div>
    <div class="acc-item"><span class="acc-toggle">+</span>Euismod Tempor</div>
    <div class="acc-item" style="border:none"><span class="acc-toggle">+</span>Incidunt Magna Aliqua.</div>
  </div>

  <div class="abs blog">
    <h2 class="section-title">From the Blog</h2>
    <div class="post"><div class="thumb" role="img" aria-label="Grasshopper on a branch" style="background:linear-gradient(#b8b0a0,#7a7060)"></div><div><h4>Cras mattis consectetur purus sit amet</h4><small>3rd Jul, 2012 <em>-4 Comments</em></small></div></div>
    <div class="post"><div class="thumb" role="img" aria-label="Insect on a stem" style="background:linear-gradient(#cfc6b0,#8a7a58)"></div><div><h4>Aenean lacinia bibendum nulla sed consectetur</h4><small>1st Jul, 2012 <em>-7 Comments</em></small></div></div>
    <div class="post"><div class="thumb" role="img" aria-label="Green grasshopper on a leaf" style="background:linear-gradient(#6aa048,#2f5a22)"></div><div><h4>Vestibulum id ligula porta felis euismod semper</h4><small>29th Jun, 2012 <em>-15 Comments</em></small></div></div>
  </div>

  <div class="abs partners">
    <h2 class="section-title">Our Partners</h2>
    <div class="slider">
      <svg class="abs" style="left:46px;top:2px" width="8" height="5"><path d="M1 4l3-3 3 3" stroke="#555" fill="none"/></svg>
      <div class="badge"><span></span></div>
      <div class="badge"><span></span></div>
      <svg class="abs" style="left:46px;bottom:2px" width="8" height="5"><path d="M1 1l3 3 3-3" stroke="#555" fill="none"/></svg>
    </div>
  </div>

  <footer class="abs footer">
    <span>Copyrights &copy; 2014 VelkorGroup.com - All Rights Reserved</span>
    <span>Privacy Policy &nbsp;|&nbsp; Terms &amp; Conditions</span>
  </footer>
</div>
</body>
</html>
```